Plakat für Verein
Zielgruppe
Wir möchten eine Veranstaltung für unseren Verein - Hinterbrunnwalder Kameradschaftsbund machen.
Aufgabenstellung
Die Party der Golden 20er
Glanz-Glamour-Lebenslust
Tanzen wie früher - Feiern wie nie
21. März - Uhrzeit: 20.30 im Saal KT
Live mit DJaneWaltraud
Dresscode: Goldene 20er - Fransen, Federn, Hosenträger, Zylinder
Farbe: Gold/Schgwarz

```html
<!DOCTYPE html>
<html lang="de">
<head>
<meta charset="utf-8">
<title>Die Party der Golden 20er – Plakat</title>
<link href="https://fonts.googleapis.com/css2?family=Limelight&family=Josefin+Slab:wght@400;600&family=Arvo:wght@700&display=swap" rel="stylesheet">
<style>
  :root {
    --backdrop: #ebebeb;
    --gold-light: #c99f58;
    --gold-mid: #b88c44;
    --gold-dark: #96721f;
    --ink: #111111;
    --rule: #3a2a10;
    --paper-white: #ffffff;
  }
  html, body {
    margin: 0;
    width: 1200px;
    height: 848px;
    overflow: hidden;
    background: var(--backdrop);
  }
  .poster {
    position: absolute;
    left: 356px;
    top: 58px;
    width: 519px;
    height: 733px;
    background:
      radial-gradient(ellipse at 50% 38%, var(--gold-light) 0%, var(--gold-mid) 60%, var(--gold-dark) 100%);
    color: var(--ink);
    box-shadow: 0 1px 4px rgba(0,0,0,0.15);
  }
  .frame {
    position: absolute;
    inset: 0;
  }
  .title {
    position: absolute;
    left: 0;
    width: 100%;
    margin: 0;
    text-align: center;
    font-family: "Limelight", serif;
    font-weight: 400;
    font-size: 45px;
    line-height: 1;
    letter-spacing: 1px;
    white-space: nowrap;
  }
  .title-line-1 { top: 54px; }
  .title-line-2 { top: 111px; }
  .title small {
    font-size: 23px;
    letter-spacing: 0;
  }
  .tagline {
    position: absolute;
    left: 0;
    width: 100%;
    margin: 0;
    text-align: center;
    font-family: "Josefin Slab", serif;
    font-weight: 600;
    line-height: 1;
    white-space: nowrap;
  }
  .tagline-main { top: 189px; font-size: 27px; }
  .tagline-sub { top: 228px; font-size: 22px; }
  .sep {
    display: inline-block;
    width: 5px;
    height: 5px;
    border: 1.5px solid var(--ink);
    vertical-align: middle;
    margin: 0 5px 4px;
  }
  .dancers {
    position: absolute;
    left: 32px;
    top: 263px;
    width: 238px;
    height: 335px;
    background: linear-gradient(180deg, rgba(17,17,17,0.5), rgba(17,17,17,0.7));
    border-radius: 6px;
  }
  .date-badge {
    position: absolute;
    left: 290px;
    top: 274px;
    width: 184px;
    height: 184px;
    border-radius: 50%;
    background: var(--ink);
    box-shadow: 0 0 0 4px var(--gold-mid), 0 0 0 9px var(--ink);
    display: flex;
    flex-direction: column;
    align-items: center;
    justify-content: center;
    color: var(--paper-white);
    font-family: "Josefin Slab", serif;
    font-weight: 600;
    font-size: 25px;
    line-height: 32px;
    letter-spacing: 1px;
    white-space: nowrap;
  }
  .live-box {
    position: absolute;
    left: 274px;
    top: 524px;
    width: 205px;
    height: 64px;
    background: var(--ink);
    color: var(--paper-white);
    clip-path: polygon(8px 0, calc(100% - 8px) 0, calc(100% - 8px) 8px, 100% 8px, 100% calc(100% - 8px), calc(100% - 8px) calc(100% - 8px), calc(100% - 8px) 100%, 8px 100%, 8px calc(100% - 8px), 0 calc(100% - 8px), 0 8px, 8px 8px);
    display: flex;
    flex-direction: column;
    align-items: center;
    justify-content: center;
    font-family: "Arvo", serif;
    font-weight: 700;
    font-size: 18px;
    line-height: 1.3;
    white-space: nowrap;
  }
  .dresscode {
    position: absolute;
    left: 0;
    top: 617px;
    width: 100%;
    margin: 0;
    text-align: center;
    font-family: "Josefin Slab", serif;
    font-weight: 600;
    font-size: 23px;
    line-height: 30px;
    white-space: nowrap;
  }
  .dresscode small { font-size: 14px; }
</style>
</head>
<body>
  <main class="poster">
    <svg class="frame" width="519" height="733" viewBox="0 0 519 733" aria-hidden="true">
      <g fill="none" stroke="#111" stroke-width="1.5">
        <rect x="25" y="22" width="469" height="689"/>
        <rect x="32" y="29" width="455" height="675"/>
        <path d="M25 52 H40 V37 H55 V22"/>
        <rect x="42" y="39" width="10" height="10"/>
        <path d="M494 52 H479 V37 H464 V22"/>
        <rect x="467" y="39" width="10" height="10"/>
        <path d="M25 681 H40 V696 H55 V711"/>
        <rect x="42" y="684" width="10" height="10"/>
        <path d="M494 681 H479 V696 H464 V711"/>
        <rect x="467" y="684" width="10" height="10"/>
      </g>
      <g stroke="#3a2a10">
        <line x1="44" y1="165" x2="254" y2="165" stroke-width="2.5"/>
        <line x1="265" y1="165" x2="475" y2="165" stroke-width="2.5"/>
        <rect x="256" y="161.5" width="7" height="7" fill="none" stroke-width="1.5"/>
      </g>
    </svg>

    <h1 class="title title-line-1">DIE PARTY</h1>
    <h1 class="title title-line-2">DER GOLDEN 20<small>ER</small></h1>

    <p class="tagline tagline-main">GLANZ<span class="sep"></span>GLAMOUR<span class="sep"></span>LEBENSLUST</p>
    <p class="tagline tagline-sub">TANZEN WIE FRÜHER<span class="sep"></span>FEIERN WIE NIE</p>

    <div class="dancers" role="img" aria-label="Schwarze Silhouette eines tanzenden Paares im Stil der 1920er Jahre: Mann mit Hut und Frau im kurzen Kleid"></div>

    <div class="date-badge">
      <span>21. MÄRZ</span>
      <span>20.30 UHR</span>
      <span>SAAL KT</span>
    </div>

    <div class="live-box">
      <span>Live mit</span>
      <span>DJaneWaltraud</span>
    </div>

    <p class="dresscode">
      GOLDENE 20<small>ER</small> DRESSCODE:<br>
      FRANSEN<span class="sep"></span>FEDERN<br>
      HOSENTRÄGER<span class="sep"></span>ZYLINDER
    </p>
  </main>
</body>
</html>
```